Business Cards Needed for Innovative Healthcare Marketing Company

We are a marketing company focused on healthcare. Our company is all about rebranding yourself renewing your image and generating results. The phoenix stands for "reborn" or "rising" which we provide new brands for our clients we take their old brands and renew it with creativity and innovation. I am looking for a business card with color dimension. I have attached an example of a card I think has the look and feel of what I am trying to accomplish. I like that the card example has black and grey font colors, I like the font placement and the small logo, I really like the use of the colors on the right those are the colors of my logo. My logo is phoenix so maybe incorporating flames similar to that design. I would like the back a solid color maybe red with an opaque version of the logo and website. As a marketing company I am always open to creative liberty!

Target Market(s)

Doctors and business professionals.

Industry/Entity Type

Marketing

Contact Information for Business Card

Valcorne Health Care Marketing
Marla Tenwick- CEO
#(512)638-2974
email-marla@valcorne.com
website- valcorne.com

Font styles to use
Sans Serif

Colors
ec1f27
f37122
ffc214
fbed22
fbf289
f04a50

Requirements
Must have
• The logo and required information
Nice to have
• icons by the information
Should not have
• child like font

```html
<!DOCTYPE html>
<html lang="en">
<head>
<meta charset="UTF-8">
<title>Valcorne Health Care Marketing — Business Card</title>
<link rel="stylesheet" href="https://fonts.googleapis.com/css2?family=Montserrat:wght@300;400;700&display=swap">
<style>
  :root {
    --stage: #2b2b2d;
    --card-red: #a3262b;
    --card-white: #ffffff;
    --brand-red: #9e2a32;
    --brand-rule: #d9b7bb;
    --accent-orange: #f39a1e;
    --flame-red: #ec1f27;
    --flame-orange: #f37122;
    --ink: #1e1e1e;
    --white: #ffffff;
  }
  * { box-sizing: border-box; margin: 0; padding: 0; }
  html, body {
    width: 1200px; height: 900px; overflow: hidden;
    background: var(--stage);
    font-family: "Montserrat", sans-serif;
  }
  .canvas { position: relative; width: 1200px; height: 900px; }

  .card {
    position: absolute;
    width: 600px; height: 343px;
    border-radius: 22px;
    overflow: hidden;
    box-shadow: 0 14px 30px rgba(0,0,0,.45);
  }

  /* Back side */
  .card-back { left: 110px; top: 80px; background: var(--card-red); color: var(--white); }
  .card-back .brand {
    position: absolute; left: 0; right: 0; top: 105px;
    display: flex; align-items: center; justify-content: center; gap: 18px;
  }
  .card-back .brand-mark {
    width: 62px; height: 62px; border-radius: 50%;
    border: 2px solid var(--white);
  }
  .card-back .brand-name {
    font-weight: 300; color: var(--white);
    line-height: 1.15;
  }
  .brand-name .line-main { display: block; font-size: 40px; letter-spacing: 2px; }
  .brand-name .line-sub { display: block; font-size: 13px; letter-spacing: 2.5px; }
  .card-back .website {
    position: absolute; left: 0; right: 0; bottom: 52px;
    text-align: center; font-size: 17px; letter-spacing: 1px; font-weight: 400;
  }

  /* Front side */
  .card-front { left: 490px; top: 455px; background: var(--card-white); }
  .card-front .brand-name {
    position: absolute; left: 42px; top: 92px;
    color: var(--brand-red); font-weight: 300;
  }
  .card-front .brand-name .line-main { font-size: 44px; letter-spacing: 2px; }
  .card-front .brand-name .line-sub {
    font-size: 13.5px; letter-spacing: 2.4px;
    border-top: 1px solid var(--brand-rule);
    padding-top: 5px; margin-top: 4px;
  }
  .person { position: absolute; left: 42px; top: 186px; }
  .person-name {
    color: var(--accent-orange); font-weight: 700;
    font-size: 21px; letter-spacing: 1px; text-transform: uppercase;
  }
  .person-title { color: var(--ink); font-size: 14px; margin-top: 1px; }
  .contact-list {
    position: absolute; left: 42px; top: 250px;
    list-style: none; color: var(--ink); font-size: 15px;
  }
  .contact-list li { display: flex; align-items: center; gap: 10px; height: 22px; }
  .contact-list svg { width: 12px; height: 12px; fill: var(--accent-orange); flex: none; }

  .hero-art {
    position: absolute; right: 52px; top: 38px;
    width: 230px; height: 230px; border-radius: 50%;
    background: radial-gradient(circle at 45% 35%, var(--flame-orange), var(--flame-red) 85%);
    opacity: .9;
  }
</style>
</head>
<body>
<div class="canvas">

  <section class="card card-back">
    <div class="brand">
      <span class="brand-mark"></span>
      <div class="brand-name">
        <span class="line-main">VALCORNE</span>
        <span class="line-sub">HEALTH CARE MARKETING</span>
      </div>
    </div>
    <p class="website">www.valcorne.com</p>
  </section>

  <section class="card card-front">
    <div class="brand-name">
      <span class="line-main">VALCORNE</span>
      <span class="line-sub">HEALTH CARE MARKETING</span>
    </div>

    <div class="person">
      <p class="person-name">Marla Tenwick</p>
      <p class="person-title">CEO</p>
    </div>

    <ul class="contact-list">
      <li>
        <svg viewBox="0 0 24 24" aria-hidden="true"><path d="M6.6 10.8a15.1 15.1 0 0 0 6.6 6.6l2.2-2.2a1 1 0 0 1 1-.25 11.4 11.4 0 0 0 3.6.57 1 1 0 0 1 1 1V20a1 1 0 0 1-1 1A17 17 0 0 1 3 4a1 1 0 0 1 1-1h3.5a1 1 0 0 1 1 1c0 1.25.2 2.46.57 3.58a1 1 0 0 1-.25 1z"/></svg>
        (512)638-2974
      </li>
      <li>
        <svg viewBox="0 0 24 24" aria-hidden="true"><path d="M2 5h20v14H2zm2 2v.5l8 5 8-5V7zm0 3v7h16v-7l-8 5z"/></svg>
        marla@valcorne.com
      </li>
      <li>
        <svg viewBox="0 0 24 24" aria-hidden="true"><path d="M12 2a10 10 0 1 0 0 20 10 10 0 0 0 0-20zm6.9 9h-3a15 15 0 0 0-1.3-6 8 8 0 0 1 4.3 6zM12 4c.9 1.2 1.8 3.6 1.9 7h-3.8C10.2 7.6 11.1 5.2 12 4zM4.1 13h3a15 15 0 0 0 1.3 6 8 8 0 0 1-4.3-6zm3-2h-3a8 8 0 0 1 4.3-6 15 15 0 0 0-1.3 6zM12 20c-.9-1.2-1.8-3.6-1.9-7h3.8c-.1 3.4-1 5.8-1.9 7zm2.6-1a15 15 0 0 0 1.3-6h3a8 8 0 0 1-4.3 6z"/></svg>
        www.valcorne.com
      </li>
    </ul>

    <div class="hero-art" role="img" aria-label="Large decorative brand emblem in red and orange flame tones"></div>
  </section>

</div>
</body>
</html>
```